Template Flyer- Corewell Stretch & Flow

I am wanting a template 1 page flyer designed to use on the back ground of newsletter (faded background) and for our advertising posters in A4, A3, for Facebook and Instagram compatibility.

I have loaded an example from another Studio called Pinegrove (file 3)- each time they have a new workshop to advertise a picture is placed in the little circle (so this is something I would want to do too where I can load a new picture each time a new workshop is running)- They have used the flyer like a water mark...I like this.

Our colour palette is what is on our logos and you can also visit our website for a feel for what we like www.corewellstretch.com.au

I need some of the designs edited a bit more and because of the time difference, there seems to be a 24hour period where we communicate with each other. May I please request another 2 days extension

Requirements
Must have
• Id like to have a picture in the back ground. My favourite back ground that has been produced so far is a background of both picture file 9 and 10 in either.
Nice to have
• 3 picture circles options to advertise the events/workshops I have each year.
• Brush stroke style circles (see picture attached)rather then smooth circles for the picture area (in a grey tone)
Should not have
• No BLACK colour writing or black circles

```html
<!DOCTYPE html>
<html lang="en">
<head>
<meta charset="utf-8">
<title>Corewell Stretch &amp; Flow – 1 Day Retreat</title>
<link href="https://fonts.googleapis.com/css2?family=Didact+Gothic&family=Montserrat:wght@600;700&display=swap" rel="stylesheet">
<style>
  :root {
    --teal: #1a8aa8;
    --ink: #3f3f3f;
    --brush: #4d4d4f;
    --rule: #9a9a9a;
    --page: #ffffff;
    --canvas: #e6e6e6;
  }
  html, body {
    margin: 0; padding: 0;
    width: 1200px; height: 1200px;
    overflow: hidden;
    background: var(--canvas);
  }
  .flyer {
    position: absolute;
    left: 200px; top: 34px;
    width: 800px; height: 1132px;
    background: var(--page);
    overflow: hidden;
    font-family: "Didact Gothic", sans-serif;
    color: var(--ink);
    box-shadow: 0 2px 12px rgba(0,0,0,.12);
  }
  .backdrop {
    position: absolute; left: 0; top: 0;
    width: 800px; height: 1027px;
    background:
      linear-gradient(90deg, rgba(255,255,255,0) 84%, rgba(150,215,220,.35) 88%, rgba(240,150,160,.35) 95%, rgba(255,255,255,0) 100%),
      linear-gradient(180deg, #f6efe7 0%, #fbf7f2 40%, #ffffff 75%, #f7f2ec 100%);
  }
  .brand {
    position: absolute; left: 120px; top: 70px;
    width: 560px; text-align: center;
    white-space: nowrap;
  }
  .brand-mark {
    display: inline-block; vertical-align: middle;
    width: 60px; height: 60px; border-radius: 50%;
    border: 4px solid var(--teal); box-sizing: border-box;
    margin-right: 14px;
  }
  .brand-name {
    display: inline-block; vertical-align: middle;
    font-family: "Didact Gothic", sans-serif;
    font-size: 38px; color: var(--teal);
    letter-spacing: .5px;
  }
  .gallery { position: absolute; left: 0; top: 0; }
  .retreat-box {
    position: absolute; left: 37px; top: 694px;
    width: 719px; height: 105px;
    border: 1px solid var(--rule); border-radius: 4px;
    box-sizing: border-box;
  }
  .retreat-title {
    position: absolute; left: 50%; top: -30px;
    transform: translateX(-50%);
    margin: 0; padding: 0 14px;
    background: #fdfbf8;
    font-family: "Montserrat", sans-serif; font-weight: 700;
    font-size: 46px; letter-spacing: 1.5px; color: var(--teal);
    white-space: nowrap; line-height: 56px;
  }
  .retreat-desc {
    position: absolute; left: 12px; right: 12px; top: 30px;
    margin: 0; font-size: 17.5px; line-height: 22.5px;
    text-align: justify;
  }
  .retreat-desc strong { font-family: "Montserrat", sans-serif; font-weight: 700; font-size: 16px; }
  .schedule {
    position: absolute; left: 0; width: 800px; top: 818px;
    margin: 0; text-align: center;
    font-family: "Montserrat", sans-serif; font-weight: 700;
    font-size: 27px; color: var(--teal); letter-spacing: .3px;
  }
  .schedule .divider { color: var(--ink); font-weight: 600; margin: 0 6px; }
  .inclusions {
    position: absolute; left: 0; width: 800px; top: 870px;
    margin: 0; text-align: center; font-size: 25px; letter-spacing: .5px;
  }
  .cost-box {
    position: absolute; left: 159px; top: 939px;
    width: 475px; height: 88px;
    border: 1px solid var(--rule); border-radius: 4px; box-sizing: border-box;
    text-align: center;
  }
  .cost-title {
    position: absolute; left: 50%; top: -17px; transform: translateX(-50%);
    margin: 0; padding: 0 10px; background: #fcfaf7;
    font-family: "Montserrat", sans-serif; font-weight: 700;
    font-size: 24px; line-height: 30px; color: var(--teal);
  }
  .price {
    margin: 0; font-size: 25px; line-height: 32px; letter-spacing: .4px;
  }
  .price:first-of-type { margin-top: 18px; }
  .price b { font-family: "Montserrat", sans-serif; font-weight: 700; color: var(--teal); }
  .contact {
    position: absolute; left: 0; top: 1027px; width: 800px; height: 105px;
    background: var(--page); font-size: 16.5px;
  }
  .contact-line {
    position: absolute; display: flex; align-items: center; gap: 8px; white-space: nowrap;
  }
  .contact-line svg { flex: none; }
  .address { left: 178px; top: 19px; }
  .phone { left: 36px; top: 48px; font-family: "Montserrat", sans-serif; font-weight: 600; font-size: 15.5px; }
  .email { left: 206px; top: 48px; }
  .web { left: 500px; top: 48px; }
</style>
</head>
<body>
<main class="flyer">
  <div class="backdrop" role="img" aria-label="Faded studio photograph with hanging beaded strands and soft teal and pink tassels"></div>

  <header class="brand">
    <span class="brand-mark"></span><span class="brand-name">Corewell Stretch &amp; Flow</span>
  </header>

  <svg class="gallery" width="800" height="680" viewBox="0 0 800 680">
    <defs>
      <linearGradient id="studioTones" x1="0" y1="0" x2="0" y2="1">
        <stop offset="0" stop-color="#f2f2f0"/>
        <stop offset=".45" stop-color="#e4e2dc"/>
        <stop offset=".7" stop-color="#c9d6b0"/>
        <stop offset="1" stop-color="#8fbccb"/>
      </linearGradient>
      <linearGradient id="doorTones" x1="0" y1="0" x2="1" y2="0">
        <stop offset="0" stop-color="#c89a63"/>
        <stop offset=".55" stop-color="#e6cfae"/>
        <stop offset="1" stop-color="#f4f0ea"/>
      </linearGradient>
      <radialGradient id="cushionTones" cx=".5" cy=".5" r=".6">
        <stop offset="0" stop-color="#cfe0c3"/>
        <stop offset=".6" stop-color="#8ec3d8"/>
        <stop offset="1" stop-color="#e8e4da"/>
      </radialGradient>
    </defs>

    <g class="photo-circle">
      <circle cx="251" cy="407" r="172" fill="url(#studioTones)" role="img" aria-label="Studio room with yoga mats, blocks and patterned bolsters"/>
      <circle cx="251" cy="407" r="176" fill="none" stroke="var(--brush)" stroke-width="7"/>
      <circle cx="249" cy="405" r="181" fill="none" stroke="var(--brush)" stroke-width="2" stroke-dasharray="60 18 30 40"/>
    </g>
    <g class="photo-circle">
      <circle cx="551" cy="287" r="125" fill="url(#doorTones)" role="img" aria-label="Carved timber door with colourful beaded tassels hanging beside it"/>
      <circle cx="551" cy="287" r="129" fill="none" stroke="var(--brush)" stroke-width="6"/>
      <circle cx="553" cy="285" r="134" fill="none" stroke="var(--brush)" stroke-width="2" stroke-dasharray="45 22 70 30"/>
    </g>
    <g class="photo-circle">
      <circle cx="536" cy="507" r="117" fill="url(#cushionTones)" role="img" aria-label="Pile of patterned meditation cushions in teal and lime"/>
      <circle cx="536" cy="507" r="121" fill="none" stroke="var(--brush)" stroke-width="6"/>
      <circle cx="534" cy="509" r="126" fill="none" stroke="var(--brush)" stroke-width="2" stroke-dasharray="55 25 35 45"/>
    </g>
  </svg>

  <section class="retreat-box">
    <h1 class="retreat-title">1 DAY RETREAT</h1>
    <p class="retreat-desc"><strong>Facilitated by:</strong> Tessa Marlowe, Jade Corrin, Elsie Hartwell A weekend full of Inspiration, guided meditation, Yoga, Pilates, relaxation, philosophy, yummy nutritious food, and empowering information to live well in the world.</p>
  </section>

  <p class="schedule">SATURDAY, 24th MARCH<span class="divider">|</span>10.00AM - 4.00PM</p>
  <p class="inclusions">LIGHT LUNCH &amp; SNACKS ARE INCLUDED</p>

  <section class="cost-box">
    <h2 class="cost-title">COST:</h2>
    <p class="price"><b>$120</b> PER PERSON</p>
    <p class="price"><b>$100</b> CONCESSION CARD HOLDERS</p>
  </section>

  <footer class="contact">
    <div class="contact-line address">
      <svg width="14" height="16" viewBox="0 0 14 16"><path d="M7 1a5 5 0 0 0-5 5c0 4 5 9 5 9s5-5 5-9a5 5 0 0 0-5-5z" fill="none" stroke="var(--teal)" stroke-width="2"/><circle cx="7" cy="6" r="1.8" fill="var(--teal)"/></svg>
      <span>17 Wattlebank St (5,531.68 mi), Ashbury Vale, Victoria 3441</span>
    </div>
    <div class="contact-line phone">
      <svg width="16" height="16" viewBox="0 0 16 16"><path d="M4 2l2 3-1.5 1.5a8 8 0 0 0 5 5L11 10l3 2-1.5 2.5C7 14 2 9 1.5 3.5z" fill="var(--teal)"/></svg>
      <span>(03) 5555 0148</span>
    </div>
    <div class="contact-line email">
      <svg width="16" height="12" viewBox="0 0 16 12"><rect x="1" y="1" width="14" height="10" fill="none" stroke="var(--teal)" stroke-width="1.6"/><path d="M1 1l7 6 7-6" fill="none" stroke="var(--teal)" stroke-width="1.6"/></svg>
      <span>info at corewellstretch.com.au</span>
    </div>
    <div class="contact-line web">
      <svg width="15" height="15" viewBox="0 0 16 16"><circle cx="8" cy="8" r="6.5" fill="none" stroke="var(--teal)" stroke-width="1.5"/><path d="M1.5 8h13M8 1.5c-3 3.5-3 9.5 0 13M8 1.5c3 3.5 3 9.5 0 13" fill="none" stroke="var(--teal)" stroke-width="1.2"/></svg>
      <span>www.corewellstretch.com.au</span>
    </div>
  </footer>
</main>
</body>
</html>
```